Coastal Learner Bureau business cards

Australian company about to start offering its services. We recruit international students to come to study English, vocational education and postgraduate courses in Australia. We help them find the institution and select the right city they want to come to Australia. We are a young, online oriented and supportive agency. Our clients are between 18 and 35 years old, mainly University students, young professionals or people with work experience. We provide much more information that any other agency offer. We administrate a Facebook group with more than 11.000 members that daily ask questions about general information when coming to Australia, while they are here and even after they leave the country

Target Market(s)

International students from South America, Central America and Europe

Industry/Entity Type

Student

Contact Information for Business Card

Tomas Bilbrea
Managing Director
tomas@kelvarin.com.au
www.kelvoria.com.au
+61 491058264
Marrowby, Australia

Font styles to use
Serif
Sans Serif

Colors

Designer to choose colors to be used in the design.

Requirements
Must have
• Horizontal design
• Standard business card size and shape. If font uses green or yellow colours, they will have to match the ones from the logo
Nice to have
• UPDATE: Use the contents of the green image to design one of the card sides. Use our logo in the background of that side as watermark.
• Passport image, or immigration stamps. A picture of the Yarra River (from Melbourne) would be cool as well.
Should not have
• Non-standard business card size and shape
• Not black as the background colour of any sides as we are not a VIP agency or a hight class service. We are orientes to young people and they like colours, pictures, something attractive.
• Vertical design
• NO YELLOW or BLACK AS THE BACKGROUND COLOUR OF ANY SIDE OF THE BIZ CARD

```html
<!DOCTYPE html>
<html lang="en">
<head>
<meta charset="utf-8">
<title>Coastal Learner Bureau business cards</title>
<link rel="stylesheet" href="https://fonts.googleapis.com/css2?family=Mulish:wght@400;600;700&display=swap">
<style>
  :root {
    --green: #146a47;
    --yellow: #eebf1f;
    --paper: #f4f4f2;
    --backdrop: #2c2f33;
  }
  * { margin: 0; padding: 0; box-sizing: border-box; }
  html, body { width: 1200px; height: 900px; overflow: hidden; }
  body {
    background: var(--backdrop);
    font-family: "Mulish", Arial, sans-serif;
    position: relative;
  }
  .card {
    position: absolute;
    width: 540px;
    height: 309px;
    background: var(--paper);
    overflow: hidden;
    box-shadow: 0 10px 30px rgba(0,0,0,.45);
  }
  .card-back { left: 600px; top: 110px; }
  .card-front { left: 60px; top: 480px; }
  .card svg.waves { position: absolute; inset: 0; width: 100%; height: 100%; }

  .brand {
    position: absolute;
    display: flex;
    align-items: center;
    gap: 8px;
    color: var(--green);
    font-weight: 700;
    font-size: 30px;
    letter-spacing: .5px;
    white-space: nowrap;
  }
  .brand-dot {
    width: 14px; height: 14px;
    border-radius: 50%;
    background: var(--yellow);
  }
  .card-back .brand { left: 50%; top: 54px; transform: translateX(-50%); }
  .tagline {
    position: absolute;
    left: 0; right: 0; top: 100px;
    text-align: center;
    color: var(--green);
    font-weight: 600;
    font-size: 15px;
  }
  .back-url {
    position: absolute;
    right: 34px; bottom: 28px;
    color: var(--yellow);
    font-size: 15px;
  }

  .card-front .brand { left: 30px; top: 30px; font-size: 26px; }
  .person {
    position: absolute;
    right: 34px; top: 92px;
    text-align: right;
  }
  .person-name { font-size: 30px; font-weight: 600; color: var(--green); line-height: 1.1; white-space: nowrap; }
  .person-name .surname { color: var(--yellow); }
  .person-role {
    font-size: 11px;
    letter-spacing: 5px;
    color: var(--green);
    margin-top: 4px;
    margin-right: -5px;
    white-space: nowrap;
  }
  .contacts {
    position: absolute;
    right: 34px; top: 178px;
    list-style: none;
  }
  .contacts li {
    display: flex;
    justify-content: flex-end;
    align-items: center;
    gap: 10px;
    color: var(--green);
    font-size: 13px;
    line-height: 24px;
    white-space: nowrap;
  }
  .contacts svg { width: 14px; height: 14px; fill: var(--yellow); flex: none; }
</style>
</head>
<body>

<section class="card card-back" aria-label="Card back">
  <svg class="waves" viewBox="0 0 540 309" preserveAspectRatio="none" aria-hidden="true">
    <path fill="var(--yellow)" d="M0,96 C70,140 170,175 330,205 C190,190 80,160 0,124 Z"/>
    <path fill="var(--green)" d="M0,134 C110,190 250,215 400,230 C470,238 520,262 540,309 L0,309 Z"/>
    <path fill="var(--paper)" d="M0,150 C60,185 130,205 230,222 C140,215 60,196 0,170 Z"/>
  </svg>
  <div class="brand"><span class="brand-dot"></span>Kelvoria</div>
  <p class="tagline">Te acompañamos siempre!</p>
  <p class="back-url">www.kelvoria.com.au</p>
</section>

<section class="card card-front" aria-label="Card front">
  <svg class="waves" viewBox="0 0 540 309" preserveAspectRatio="none" aria-hidden="true">
    <path fill="var(--green)" d="M0,130 C90,140 150,190 190,250 C215,290 270,309 360,309 L0,309 Z"/>
    <path fill="var(--paper)" d="M30,138 C90,160 130,200 150,250 C120,205 80,170 30,138 Z"/>
    <path fill="var(--yellow)" d="M170,195 C210,260 270,300 400,309 L360,309 C280,305 225,280 195,240 Z"/>
  </svg>
  <div class="brand"><span class="brand-dot"></span>Kelvoria</div>
  <div class="person">
    <p class="person-name">Tomas <span class="surname">Bilbrea</span></p>
    <p class="person-role">Managing Director</p>
  </div>
  <ul class="contacts">
    <li>Marrowby, Australia
      <svg viewBox="0 0 24 24" aria-hidden="true"><path d="M12 2a7 7 0 0 0-7 7c0 5 7 13 7 13s7-8 7-13a7 7 0 0 0-7-7zm0 9.5A2.5 2.5 0 1 1 12 6.5a2.5 2.5 0 0 1 0 5z"/></svg></li>
    <li>+61 491058264
      <svg viewBox="0 0 24 24" aria-hidden="true"><path d="M6.6 10.8a15 15 0 0 0 6.6 6.6l2.2-2.2a1 1 0 0 1 1-.25 11 11 0 0 0 3.6.6 1 1 0 0 1 1 1V20a1 1 0 0 1-1 1A17 17 0 0 1 3 4a1 1 0 0 1 1-1h3.5a1 1 0 0 1 1 1 11 11 0 0 0 .6 3.6 1 1 0 0 1-.25 1z"/></svg></li>
    <li>www.kelvoria.com.au
      <svg viewBox="0 0 24 24" aria-hidden="true"><path d="M12 2a10 10 0 1 0 0 20 10 10 0 0 0 0-20zm-1 17.9A8 8 0 0 1 4.1 11H7c.1 3.2.9 6.4 4 8.9zM7 9H4.1A8 8 0 0 1 11 4.1C8 6.6 7.1 6 7 9zm6 10.9c3.1-2.5 3.9-5.7 4-8.9h2.9a8 8 0 0 1-6.9 8.9zM17 9c-.1-3-1-2.4-4-4.9A8 8 0 0 1 19.9 9zm-8 2h6c-.1 3-1 5.6-3 7.6-2-2-2.9-4.6-3-7.6zm0-2c.1-3 1-5.6 3-7.6 2 2 2.9 4.6 3 7.6z"/></svg></li>
    <li>tomas@kelvarin.com.au
      <svg viewBox="0 0 24 24" aria-hidden="true"><path d="M3 5h18a1 1 0 0 1 1 1v12a1 1 0 0 1-1 1H3a1 1 0 0 1-1-1V6a1 1 0 0 1 1-1zm9 7.5L20 7H4z"/></svg></li>
  </ul>
</section>

</body>
</html>
```